New Business Card Design Project

Use the flyer uploaded and website www.brightoakbuilders.com for inspiration.
List Our Services on Backside of business cards
Marcus Delling
Harborline Builders Inc.
Licensed General Contractors
858-471-6093

Contact Information for Business Card

Use the flyer uploaded and website www.brightoakbuilders.com for inspiration. List Our Services on Backside of business cards Marcus Delling Harborline Builders Inc. Licensed General Contractors 858-471-6093

```html
<!DOCTYPE html>
<html lang="en">
<head>
<meta charset="utf-8">
<title>Harborline Builders – Business Cards</title>
<link rel="stylesheet" href="https://fonts.googleapis.com/css2?family=Montserrat:wght@300;400;500;700;800&display=swap">
<style>
  :root {
    --bg: #e9e7e3;
    --card-dark: #2c2c2e;
    --card-dark-hi: #4a4a4d;
    --card-dark-lo: #1c1c1e;
    --card-light: #ffffff;
    --ink: #1d1d1f;
    --ink-soft: #3a3a3c;
    --on-dark: #f2f2f2;
    --accent: #f5b400;
  }
  * { box-sizing: border-box; margin: 0; padding: 0; }
  html, body { width: 1200px; height: 913px; overflow: hidden; }
  body {
    background: var(--bg);
    font-family: "Montserrat", Arial, sans-serif;
    position: relative;
  }
  .card {
    position: absolute;
    top: 306px;
    width: 525px;
    height: 300px;
    border-radius: 3px;
    overflow: hidden;
    box-shadow: 0 10px 24px rgba(0,0,0,.18);
  }

  /* Back card: services */
  .card-back {
    left: 60px;
    background: linear-gradient(115deg, var(--card-dark-lo) 0%, var(--card-dark) 35%, var(--card-dark-hi) 70%, var(--card-dark) 100%);
  }
  .card-back .decor {
    position: absolute;
    left: 0; top: 0;
    width: 230px; height: 300px;
    background: radial-gradient(ellipse at 40% 40%, rgba(200,200,200,.28), rgba(40,40,40,0) 70%);
  }
  .card-back .wordmark {
    position: absolute;
    left: 225px; top: 40px;
    color: var(--on-dark);
    font-weight: 300;
    font-size: 21px;
    letter-spacing: 2px;
    text-transform: uppercase;
  }
  .card-back .services { position: absolute; left: 245px; top: 88px; color: var(--on-dark); }
  .services-title {
    font-weight: 700;
    font-size: 15px;
    padding-bottom: 6px;
    margin-bottom: 8px;
    border-bottom: 1px solid rgba(255,255,255,.6);
    width: 110px;
  }
  .services-list { list-style: none; font-size: 11.5px; font-weight: 400; line-height: 17px; }
  .services-list li::before { content: "•"; margin-right: 7px; }

  /* Front card: contact */
  .card-front { left: 615px; background: var(--card-light); }
  .card-front .brand-panel {
    position: absolute; right: 0; top: 0;
    width: 235px; height: 300px;
    background: var(--card-dark);
    display: flex; align-items: center; justify-content: center;
  }
  .brand-panel .wordmark {
    color: var(--on-dark);
    font-weight: 300;
    font-size: 15px;
    letter-spacing: 2px;
    text-transform: uppercase;
    text-align: center;
    line-height: 1.4;
  }
  .contact { position: absolute; left: 30px; top: 40px; color: var(--ink); }
  .person-name { font-weight: 800; font-size: 24px; letter-spacing: .3px; }
  .person-role { font-size: 12px; color: var(--ink-soft); margin-top: 2px; }
  .details { margin-top: 60px; font-size: 12px; line-height: 17px; color: var(--ink-soft); }
  .details .license { margin-top: 10px; margin-bottom: 8px; }
  .details .line { display: flex; align-items: center; gap: 10px; margin-top: 4px; }
  .details svg { width: 12px; height: 12px; fill: var(--ink); flex: none; }
</style>
</head>
<body>

  <section class="card card-back" aria-label="Card back: services">
    <div class="decor" role="img" aria-label="Faded palm tree decoration"></div>
    <div class="wordmark">Harborline Builders</div>
    <div class="services">
      <h2 class="services-title">Our Services</h2>
      <ul class="services-list">
        <li>Remodel Kitchen &amp; Bath</li>
        <li>Painting Interior &amp; Exterior</li>
        <li>Flooring Carpet, Vinyl, Wood</li>
        <li>Window/ Door Replacement</li>
        <li>Plumbing Repair &amp; Upgrades</li>
        <li>Energy Efficient Upgrades</li>
        <li>Deck &amp; Patio construction</li>
        <li>Water &amp; Mold Damage</li>
        <li>Garage Renovation</li>
      </ul>
    </div>
  </section>

  <section class="card card-front" aria-label="Card front: contact">
    <div class="contact">
      <h1 class="person-name">Marcus Delling</h1>
      <p class="person-role">Managing Director</p>
      <div class="details">
        <p>240 Cedar Ridge Road<br>Fairview, MS 39200</p>
        <p class="license">CSLB Licensed No. #2046815</p>
        <p class="line">
          <svg viewBox="0 0 24 24" aria-hidden="true"><path d="M6.6 10.8a15.1 15.1 0 0 0 6.6 6.6l2.2-2.2a1 1 0 0 1 1-.25 11.4 11.4 0 0 0 3.6.57 1 1 0 0 1 1 1V20a1 1 0 0 1-1 1A17 17 0 0 1 3 4a1 1 0 0 1 1-1h3.5a1 1 0 0 1 1 1c0 1.25.2 2.45.57 3.57a1 1 0 0 1-.25 1z"/></svg>
          858-471-6093
        </p>
        <p class="line">
          <svg viewBox="0 0 24 24" aria-hidden="true"><path d="M2 5h20v14H2z M2 5l10 8 10-8" fill="none" stroke="#1d1d1f" stroke-width="2.4"/></svg>
          info@brightoakbuilders.com
        </p>
        <p class="line">
          <svg viewBox="0 0 24 24" aria-hidden="true"><circle cx="12" cy="12" r="9.5" fill="none" stroke="#1d1d1f" stroke-width="2.2"/><path d="M2.5 12h19M12 2.5c3 3 3 16 0 19M12 2.5c-3 3-3 16 0 19" fill="none" stroke="#1d1d1f" stroke-width="1.8"/></svg>
          www.brightoakbuilders.com
        </p>
      </div>
    </div>
    <div class="brand-panel">
      <div class="wordmark">Harborline<br>Builders</div>
    </div>
  </section>

</body>
</html>
```